TalbeckLabs needs a new rocket based website

We need a new website that will be based on our rocket ship logo. We develop innovative solutions for enterprises. We would like to see a design that when the pages scroll, the rocket launches and goes from launch through a journey, similar to how we approach our customer. We would like areas for "Who are we", "What can we do", "What have we done", "How can we help". http://www.talbecklabs.example.au is our current website

Target Market(s)

Government, Enterprise, Cloud

Industry/Entity Type

Software Service

Coding

Coded - Design and coding required

Number of Pages Required

2 page

Requirements
Must have
• We would like to see a design that when the pages scroll, the rocket launches and goes from launch through a journey, similar to how we approach our customer.
• Must have a home page and a detail page.
• Would like to see the logo/rocket animate in some way when you scroll through he page.

```html
<!DOCTYPE html>
<html lang="en">
<head>
<meta charset="utf-8">
<title>TalbeckLabs – Innovative Solutions for Enterprise</title>
<link href="https://fonts.googleapis.com/css2?family=Exo+2:wght@500;600;700&family=Montserrat:wght@500;600&family=Arimo:wght@400;700&display=swap" rel="stylesheet">
<style>
  :root{
    --orange:#f28322;
    --ink:#2a2a2a;
    --body:#555555;
    --white:#ffffff;
    --footer:#1d1d1d;
    --rule:#3a3a3a;
    --ring:#cfcfcf;
    --hero-a:#3b3f44;
    --hero-b:#6a5a50;
  }
  *{box-sizing:border-box;margin:0;padding:0}
  html,body{width:1200px;height:2778px;overflow:hidden;background:var(--white)}
  body{position:relative;font-family:"Arimo",Arial,sans-serif;color:var(--body);-webkit-font-smoothing:antialiased;-moz-osx-font-smoothing:grayscale}

  /* header */
  .site-header{position:absolute;left:0;top:0;width:1200px;height:104px;background:var(--white);border-top:4px solid var(--orange)}
  .brand{position:absolute;display:flex;align-items:center;gap:10px;font-family:"Exo 2",sans-serif;font-weight:700;color:var(--orange)}
  .brand-dot{width:14px;height:14px;border-radius:50%;background:var(--orange)}
  .site-header .brand{left:111px;top:30px;font-size:34px}
  .main-nav{position:absolute;top:46px;font-family:"Montserrat",sans-serif;font-weight:500;font-size:13px;color:#222;letter-spacing:.3px}
  .main-nav a{position:absolute;white-space:nowrap;color:inherit;text-decoration:none}
  .main-nav a.active{color:var(--orange)}

  /* hero */
  .hero{position:absolute;left:0;top:104px;width:1200px;height:572px;background:linear-gradient(100deg,#2c3136 0%,var(--hero-a) 40%,var(--hero-b) 75%,#8a7160 100%)}
  .hero-title{position:absolute;left:189px;top:180px;font-family:"Exo 2",sans-serif;font-weight:600;font-size:58px;color:var(--white);letter-spacing:1px}
  .hero-text{position:absolute;left:192px;top:264px;width:430px;font-size:12px;line-height:26px;color:var(--white)}
  .btn{position:absolute;display:flex;align-items:center;justify-content:center;background:var(--orange);color:var(--white);font-family:"Montserrat",sans-serif;font-weight:600;text-transform:uppercase;text-decoration:none}
  .hero .btn{left:193px;top:370px;width:142px;height:46px;font-size:16px}
  .slider-arrow{position:absolute;top:268px;width:34px;height:34px;border:2px solid var(--white);border-radius:50%}
  .slider-arrow svg{position:absolute;left:8px;top:8px}

  /* journey */
  .launch-pad{position:absolute;left:554px;top:639px;width:92px;height:92px;border-radius:50%;background:var(--white)}
  .launch-pad .brand-dot{position:absolute;left:33px;top:33px;width:26px;height:26px}
  .journey-line{position:absolute;left:599px;top:750px;height:1010px;border-left:2px dotted #b8b8b8}
  .journey-end{position:absolute;left:594px;top:1757px;width:12px;height:12px;border-radius:50%;background:var(--orange)}

  .section-title{position:absolute;font-family:"Exo 2",sans-serif;font-weight:700;font-size:31px;color:var(--ink);letter-spacing:.5px;text-transform:uppercase}
  .section-title span{color:var(--orange)}
  .section-text{position:absolute;width:455px;font-size:12px;line-height:26px;color:var(--body);text-align:justify}
  .section .btn{height:41px;font-size:14px}
  .photo{position:absolute;width:452px;height:260px}

  /* services */
  .services{position:absolute;left:0;top:1822px;width:1200px;height:354px;background:var(--orange);color:var(--white);text-align:center}
  .services h2{position:absolute;left:0;width:1200px;top:30px;font-family:"Exo 2",sans-serif;font-weight:600;font-size:30px;letter-spacing:1px}
  .services .underline{position:absolute;left:556px;top:76px;width:88px;height:3px;background:var(--white)}
  .service{position:absolute;top:121px;width:240px}
  .service .ring{margin:0 auto;width:104px;height:104px;border:2px solid var(--white);border-radius:50%;display:flex;align-items:center;justify-content:center}
  .service h3{margin-top:22px;font-family:"Montserrat",sans-serif;font-weight:600;font-size:14px;letter-spacing:.5px}
  .service p{margin-top:10px;font-size:12px;line-height:22px}

  /* testimonial */
  .quote-mark{position:absolute;font-family:Georgia,serif;font-size:36px;color:#aaa}
  .quote-text{position:absolute;left:185px;top:2262px;width:540px;font-size:12px;line-height:23px;color:var(--body)}
  .quote-name{position:absolute;left:187px;top:2382px;font-weight:700;font-size:15px;color:var(--orange)}
  .quote-date{position:absolute;left:187px;top:2405px;font-size:12px;color:var(--body)}
  .avatar{position:absolute;left:783px;top:2232px;width:196px;height:196px;border-radius:50%;border:4px solid #e6e6e6;background:radial-gradient(circle at 50% 40%,#c89a80,#7a5542 70%,#d9d9d9 100%)}

  /* footer */
  .site-footer{position:absolute;left:0;top:2482px;width:1200px;height:296px;background:var(--footer)}
  .site-footer .brand{left:0;width:1200px;justify-content:center;top:48px;font-size:38px}
  .footer-rule{position:absolute;left:111px;top:135px;width:978px;height:1px;background:var(--rule)}
  .social{position:absolute;top:157px;width:60px;height:60px;border:1.5px solid var(--ring);border-radius:50%;display:flex;align-items:center;justify-content:center;font-size:11px;font-weight:700;color:var(--white);text-transform:uppercase;letter-spacing:.3px}
  .copyright{position:absolute;left:0;top:248px;width:1200px;text-align:center;font-size:12px;color:#ddd}
</style>
</head>
<body>

<header class="site-header">
  <div class="brand"><span class="brand-dot"></span>TalbeckLabs</div>
  <nav class="main-nav">
    <a class="active" style="left:541px">HOME</a>
    <a style="left:638px">ABOUT US</a>
    <a style="left:755px">SERVICES</a>
    <a style="left:871px">TESTIMONIALS</a>
    <a style="left:1014px">CONTACT US</a>
  </nav>
</header>

<section class="hero" role="img" aria-label="Photo of developers working together at computer screens">
  <div class="slider-arrow" style="left:63px"><svg width="14" height="14" viewBox="0 0 14 14"><path d="M9 2 L4 7 L9 12" fill="none" stroke="#fff" stroke-width="2"/></svg></div>
  <div class="slider-arrow" style="left:1097px"><svg width="14" height="14" viewBox="0 0 14 14"><path d="M5 2 L10 7 L5 12" fill="none" stroke="#fff" stroke-width="2"/></svg></div>
  <h1 class="hero-title">TALBECKLABS</h1>
  <p class="hero-text">Sed ut perspiciatis unde omnis iste natus error sit voluptatem accusantium doloremque laudantium, totam rem aperiam, eaque ipsa quae ab illo inventore veritatis et quasi architecto beatae vitae dicta sunt explicabo.</p>
  <a class="btn">Read More</a>
</section>

<div class="launch-pad"><span class="brand-dot"></span></div>
<div class="journey-line"></div>
<div class="journey-end"></div>

<section class="section who">
  <h2 class="section-title" style="left:111px;top:776px">Who <span>are we</span></h2>
  <p class="section-text" style="left:111px;top:838px">Sed ut perspiciatis unde omnis iste natus error sit voluptatem accusantium dolorem que laudantium, totam rem aperiam, eaque ipsa quae ab illo inventore veritatis et quasi architecto beatae vitae dicta sunt explicabo. Nemo enim ipsam voluptatem quia voluptas sit aspernatur aut odit aut fugit, sed quia consequuntur magni dolores eos qui quisquam est, qui dolorem ratione voluptatem sequi nesciunt.</p>
  <a class="btn" style="left:111px;top:991px;width:116px">Read More</a>
  <div class="photo" role="img" aria-label="Photo of two colleagues reviewing work on a monitor" style="left:636px;top:787px;background:linear-gradient(120deg,#2c4a6e,#5a6e86 50%,#b49d88)"></div>
</section>

<section class="section done">
  <div class="photo" role="img" aria-label="Photo of hands typing code on a laptop keyboard" style="left:111px;top:1126px;background:linear-gradient(180deg,#cfd8e0,#5d7288 55%,#1f2730)"></div>
  <h2 class="section-title" style="left:635px;top:1114px">What have <span>we done</span></h2>
  <p class="section-text" style="left:636px;top:1178px">Sed ut perspiciatis unde omnis iste natus error sit voluptatem accusantium dolorem que laudantium, totam rem aperiam, eaque ipsa quae ab illo inventore veritatis et quasi architecto beatae vitae dicta sunt explicabo. Nemo enim ipsam voluptatem quia voluptas sit aspernatur aut odit aut fugit, sed quia consequuntur magni dolores eos qui quisquam est, qui dolorem ratione voluptatem sequi nesciunt.</p>
  <a class="btn" style="left:635px;top:1330px;width:167px">See our projects</a>
</section>

<section class="section help">
  <h2 class="section-title" style="left:111px;top:1456px">How can <span>we help</span></h2>
  <p class="section-text" style="left:111px;top:1519px">Sed ut perspiciatis unde omnis iste natus error sit voluptatem accusantium dolorem que laudantium, totam rem aperiam, eaque ipsa quae ab illo inventore veritatis et quasi architecto beatae vitae dicta sunt explicabo. Nemo enim ipsam voluptatem quia voluptas sit aspernatur aut odit aut fugit, sed quia consequuntur magni dolores eos qui quisquam est, qui dolorem ratione voluptatem sequi nesciunt.</p>
  <a class="btn" style="left:111px;top:1672px;width:116px">Contact Us</a>
  <div class="photo" role="img" aria-label="Photo of a developer with headphones working in an open office" style="left:636px;top:1469px;background:linear-gradient(110deg,#d8d2cc,#8c8580 45%,#3e4a5a 75%,#c56a3a)"></div>
</section>

<section class="services">
  <h2>WHAT WE DO</h2>
  <div class="underline"></div>
  <div class="service" style="left:110px">
    <div class="ring"><svg width="52" height="52" viewBox="0 0 52 52" fill="none" stroke="#fff" stroke-width="2"><path d="M6 18 L26 6 L46 18 Z"/><path d="M10 22 H42 M10 44 H42 M6 48 H46"/><path d="M15 24 V42 M23 24 V42 M29 24 V42 M37 24 V42"/></svg></div>
    <h3>E-PARLIAMENT</h3>
    <p>All of your Parliamentary software and<br>business process needs.</p>
  </div>
  <div class="service" style="left:358px">
    <div class="ring"><svg width="56" height="52" viewBox="0 0 56 52" fill="none" stroke="#fff" stroke-width="2"><path d="M14 32 A9 9 0 0 1 16 14 A12 12 0 0 1 38 12 A10 10 0 0 1 44 32 Z"/><path d="M28 32 V42 M18 46 H38 M28 42 V46"/></svg></div>
    <h3>CLOUD</h3>
    <p>Hosted Office Suites, Migration,<br>Security, Customisations</p>
  </div>
  <div class="service" style="left:606px">
    <div class="ring"><svg width="52" height="56" viewBox="0 0 52 56" fill="none" stroke="#fff" stroke-width="2"><circle cx="26" cy="10" r="4"/><path d="M26 2 V6 M24 14 L12 50 M28 14 L40 50 M16 36 Q26 42 36 36"/></svg></div>
    <h3>ARCHITECTURE &amp; DESIGN</h3>
    <p>Business process design, technology<br>strategy and architecture.</p>
  </div>
  <div class="service" style="left:854px">
    <div class="ring"><svg width="56" height="52" viewBox="0 0 56 52" fill="none" stroke="#fff" stroke-width="2"><rect x="12" y="8" width="32" height="26" rx="2"/><path d="M6 40 H50 L46 44 H10 Z"/><path d="M24 15 L20 21 L24 27 M32 15 L36 21 L32 27"/></svg></div>
    <h3>SOFTWARE DEVELOPMENT</h3>
    <p>Software development including<br>business apps, web and mobile.</p>
  </div>
</section>

<section class="testimonial">
  <span class="quote-mark" style="left:166px;top:2236px">&ldquo;</span>
  <p class="quote-text">Sed ut perspiciatis unde omnis iste natus error sit voluptatem accusantium doloremque laudantium, totam rem aperiam, eaque ipsa quae ab illo inventore veritatis et quasi architecto beatae vitae dicta sunt explicabo. Nemo enim ipsam voluptatem quia voluptas sit aspernatur aut odit aut fugit, sed quia consequuntur magni dolores eos qui ratione voluptatem sequi nesciunt.</p>
  <span class="quote-mark" style="left:570px;top:2342px">&rdquo;</span>
  <div class="quote-name">MARA QUINLAN</div>
  <div class="quote-date">Posted On 07 July 2018</div>
  <div class="avatar" role="img" aria-label="Portrait photo of the client giving the testimonial"></div>
</section>

<footer class="site-footer">
  <div class="brand"><span class="brand-dot"></span>TalbeckLabs</div>
  <div class="footer-rule"></div>
  <a class="social" style="left:386px">Like</a>
  <a class="social" style="left:458px">Post</a>
  <a class="social" style="left:529px">Plus</a>
  <a class="social" style="left:601px">Work</a>
  <a class="social" style="left:672px">Pics</a>
  <a class="social" style="left:744px" aria-label="Email"><svg width="18" height="14" viewBox="0 0 18 14" fill="none" stroke="#fff" stroke-width="1.5"><rect x="1" y="1" width="16" height="12"/><path d="M1 1 L9 8 L17 1"/></svg></a>
  <p class="copyright">© Copyrights 2018 - TalbeckLabs.All Rights Reserved.</p>
</footer>

</body>
</html>
```